High-Converting Facebook Ads for Portals Drapes & Louvres (6 Products)

We are looking for a graphic designer to create high-quality Facebook & Instagram ads for our business: Portals Drapes and Louvres (Melbourne, Australia).

We require 6 separate ad designs, each for a different product:

Zipscreen Blinds

Outdoor Awnings

Plantation Shutters

Roller Shutters

Security Doors

Roller Blinds & Sheer Curtains

Ad Specifications:

Sizes:

1440 x 1800 px (4:5 ratio)

1080 x 1080 px (1:1 ratio)

1080 x 1920 px (9:16 ratio for Stories/Reels)

Format: PNG (high resolution, not blurry)

Designed specifically for Meta (Facebook/Instagram ads)

Mobile-friendly layout (clear, easy to read)

Style:

Bold, sales-driven, retail-style ads (NOT minimal)

Eye-catching and designed to generate leads

Clean, professional layout

Similar to promotional home improvement ads

Brand Colours:

Red: #E31E24

Blue: #0072BC

White backgrounds

Each ad must include:

“SALE NOW ON” banner at top

Our showroom address:
482 Upper Wattleby Road, Kestrel Heights (must be fully visible, not cut off)

Phone number: 9471 2658

Our logo (provided)

Badge: “Celebrating 13 YEARS in Business” (must be clean and readable)

Call to Action:

For 5 ads: “Book a FREE quote TODAY!”

For Security Doors ad: “ORDER NOW”

Offers / Pricing:

Most products: “UP TO 40% OFF”

Plantation Shutters: “FROM $299/sqm”

Security Doors: “FROM $750”

Content for each ad (examples):

Zipscreen Blinds:

Made to Measure

Fully Installed

Wind, Sun & Insect Protection

Outdoor Awnings:

Reduce Heat & Glare

Energy Saving

Custom Made

Plantation Shutters:

Modern & Elegant

Light & Privacy Control

Durable & Easy Care

Roller Shutters:

Security Protection

Block Heat & Noise

Total Light Control

Security Doors:

3 Point Locking

Premium Mesh

Custom Made

Blinds & Sheers:

Huge Range of Fabrics

Modern Soft Finish

Perfect for Any Room

Important Notes:

All text must be sharp and easy to read (no blur)

Layout must be balanced and not overcrowded

Ensure no text is cut off (especially address and headings)

Badge text must be straight and professional (no distortion)

Use high-quality, relevant images (we will provide references)

Goal:
Create ads that look professional, trustworthy, and generate enquiries/bookings for in-home quotes.

We are open to creative ideas but want a strong, bold retail-style ad that converts.
I have uploaed chatgpt mocks

Target Market(s)

Homeowners in Melbourne, Australia (typically aged 30–65) looking to improve their homes with blinds, shutters, awnings and security doors. Mid to high income households focused on quality, security, and modern home upgrades.

Industry/Entity Type

Home Improvement / Construction / Retail

Font styles to use
Sans Serif

Requirements
Must have
• Clear, bold and easy-to-read text (must be readable on mobile) High-quality, non-blurry design Strong “SALE” style layout (retail promotional look) Proper spacing (no overcrowded designs) All key info visible (address must NOT be cut off) Correct pricing and offers included Clean “13 YEARS” badge (no distortion or curved text) Consistent branding across all 6 ads
Nice to have
• Modern, slightly premium feel while still being bold Good use of contrast (red/blue/white) Subtle shadows or layering to improve depth Clean use of icons or bullet points Strong hierarchy (headline → benefits → offer → CTA) Variations in layout for testing different ad styles
Should not have
• Minimal or plain designs (we want bold, sales-driven ads) Hard-to-read fonts or script fonts Low-quality or blurry images Overcrowded layouts with too much text Important text cut off (especially address or headings) Overuse of effects or “cheap” looking graphics Yellow-heavy colour schemes (must follow brand colours)

```html
<!DOCTYPE html>
<html lang="en">
<head>
<meta charset="utf-8">
<title>Portals Drapes &amp; Louvres – Story Ads 9:16</title>
<link href="https://fonts.googleapis.com/css2?family=Anton&family=Oswald:wght@400;500;600&family=Tinos:wght@700&family=Archivo+Black&display=swap" rel="stylesheet">
<style>
  :root{
    --brand-red:#e31e24;
    --brand-blue:#0072bc;
    --deep-blue:#0a5fa8;
    --ink:#1b1b1b;
    --white:#ffffff;
    --board:#2a2a2a;
    --ribbon-tint:#c9dcee;
  }
  *{margin:0;padding:0;box-sizing:border-box}
  html,body{width:1073px;height:1200px;overflow:hidden;background:var(--board)}
  .stage{position:absolute;left:0;top:0;width:1820px;height:2035px;transform:scale(0.58956);transform-origin:0 0}
  .size-label{position:absolute;top:128px;left:0;width:100%;text-align:center;color:var(--white);
    font-family:"Oswald",sans-serif;font-weight:500;font-size:38px;letter-spacing:.5px}
  .ad{position:absolute;width:440px;height:781px;background:var(--white);overflow:hidden}
  .ad.c1{left:215px}.ad.c2{left:690px}.ad.c3{left:1165px}
  .ad.r1{top:266px}.ad.r2{top:1067px}
  .sale-banner{position:absolute;left:0;top:0;width:100%;height:75px;background:var(--brand-blue);
    color:var(--white);font-family:"Tinos",serif;font-weight:700;font-size:54px;text-align:center;line-height:76px;letter-spacing:.5px}
  .hero{position:absolute;left:0;top:0;width:440px;height:781px}
  .brand-name{position:absolute;left:30px;top:268px;width:200px;text-align:center;color:var(--white);
    font-family:"Oswald",sans-serif;font-weight:500;font-size:26px;line-height:28px}
  .brand-name .mark{display:block;width:34px;height:34px;margin:0 auto 8px;border:4px solid var(--white)}
  .product-ribbon{position:absolute;left:28px;top:452px;width:270px;height:40px;
    background:linear-gradient(90deg,rgba(201,220,238,0) 0%,var(--ribbon-tint) 25%,var(--ribbon-tint) 70%,rgba(201,220,238,0) 100%);
    color:var(--deep-blue);font-family:"Oswald",sans-serif;font-weight:500;font-size:28px;line-height:40px;text-align:center}
  .benefits{position:absolute;top:499px;list-style:none;font-family:"Oswald",sans-serif;font-weight:500;font-size:19px;color:var(--ink)}
  .benefits li{height:28px;line-height:28px;display:flex;align-items:center;white-space:nowrap}
  .benefits li::before{content:"";width:13px;height:11px;margin-right:12px;
    background:repeating-linear-gradient(180deg,var(--brand-red) 0 2px,#f4b6b8 2px 3px);border-left:2px solid var(--brand-red)}
  .offer{position:absolute;left:0;top:588px;width:100%;text-align:center;font-family:"Anton",sans-serif;font-size:62px;line-height:72px;color:var(--brand-blue);letter-spacing:-.5px;white-space:nowrap}
  .offer em{font-style:normal;color:var(--brand-red)}
  .cta{position:absolute;left:0;top:660px;width:100%;height:63px;background:var(--brand-red);color:var(--white);
    text-align:center;font-family:"Oswald",sans-serif;font-weight:600;font-size:38px;line-height:62px}
  .cta.order{font-family:"Tinos",serif;font-weight:700;font-size:54px;letter-spacing:1px}
  .contact-bar{position:absolute;left:0;top:723px;width:100%;height:58px;background:var(--brand-blue);color:var(--white)}
  .phone{position:absolute;left:18px;top:8px;font-family:"Archivo Black",sans-serif;font-size:31px;line-height:42px;display:flex;align-items:center;gap:6px}
  .phone svg{width:16px;height:16px}
  .address{position:absolute;left:262px;top:10px;font-family:"Oswald",sans-serif;font-weight:500;font-size:13.5px;line-height:19px;padding-left:20px}
  .address svg{position:absolute;left:0;top:2px;width:14px;height:18px}
</style>
</head>
<body>
<svg width="0" height="0" style="position:absolute" aria-hidden="true">
  <defs>
    <clipPath id="photo-clip"><path d="M0,75 H400 C392,250 260,410 0,446 Z"/></clipPath>
    <linearGradient id="ph-zip" x1="0" y1="0" x2="1" y2="1"><stop offset="0" stop-color="#6f7a74"/><stop offset=".6" stop-color="#9aa39d"/><stop offset="1" stop-color="#c7c9c4"/></linearGradient>
    <linearGradient id="ph-awning" x1="0" y1="0" x2="1" y2="1"><stop offset="0" stop-color="#6f9bd0"/><stop offset=".6" stop-color="#a9c4e2"/><stop offset="1" stop-color="#8a8f96"/></linearGradient>
    <linearGradient id="ph-shutter" x1="0" y1="0" x2="1" y2="1"><stop offset="0" stop-color="#a2a8b1"/><stop offset=".6" stop-color="#c8ccd2"/><stop offset="1" stop-color="#e6e8ea"/></linearGradient>
    <linearGradient id="ph-roller" x1="0" y1="0" x2="1" y2="1"><stop offset="0" stop-color="#d5d7d8"/><stop offset=".6" stop-color="#eceded"/><stop offset="1" stop-color="#b7bbbd"/></linearGradient>
    <linearGradient id="ph-security" x1="0" y1="0" x2="1" y2="1"><stop offset="0" stop-color="#4a3424"/><stop offset=".5" stop-color="#8fa0a8"/><stop offset="1" stop-color="#6c7f6a"/></linearGradient>
    <linearGradient id="ph-sheer" x1="0" y1="0" x2="1" y2="1"><stop offset="0" stop-color="#c5c3c0"/><stop offset=".5" stop-color="#6f6a66"/><stop offset="1" stop-color="#d9d7d3"/></linearGradient>
    <g id="swoosh">
      <path d="M250,75 H440 V385 C400,360 360,335 330,318 Z" fill="#0072bc"/>
      <path d="M415,75 H440 V232 C385,335 250,430 0,470 V446 C210,425 385,300 415,75 Z" fill="#e31e24"/>
    </g>
    <g id="red-wash" clip-path="url(#photo-clip)">
      <ellipse cx="120" cy="420" rx="330" ry="205" fill="#e31e24" fill-opacity=".82"/>
    </g>
    <g id="anniversary-badge">
      <circle cx="357" cy="427" r="66" fill="#ffffff" stroke="#0072bc" stroke-width="6"/>
      <circle cx="357" cy="427" r="57" fill="none" stroke="#e31e24" stroke-width="2"/>
      <text x="357" y="393" text-anchor="middle" font-family="Oswald, sans-serif" font-weight="600" font-size="12" fill="#0a5fa8" letter-spacing="1">CELEBRATING</text>
      <text x="357" y="424" text-anchor="middle" font-family="Anton, sans-serif" font-size="28" fill="#e31e24">13</text>
      <path d="M281,429 H433 L426,441 L433,453 H281 L288,441 Z" fill="#e31e24"/>
      <text x="357" y="448" text-anchor="middle" font-family="Archivo Black, sans-serif" font-size="19" fill="#ffffff">YEARS</text>
      <text x="357" y="470" text-anchor="middle" font-family="Oswald, sans-serif" font-weight="600" font-size="13" fill="#0a5fa8" letter-spacing="1">in BUSINESS</text>
    </g>
    <g id="icon-phone"><path d="M4,2 L7,2 L8,6 L6,7 C7,9.5 8.5,11 11,12 L12,10 L16,11 L16,14 C9,15 3,9 4,2 Z" fill="#fff"/></g>
    <g id="icon-pin"><path d="M7,0 C3,0 0,3 0,7 C0,11 7,18 7,18 C7,18 14,11 14,7 C14,3 11,0 7,0 Z M7,4 A3,3 0 1,1 7,10 A3,3 0 1,1 7,4 Z" fill="#fff" fill-rule="evenodd"/></g>
  </defs>
</svg>

<div class="stage">
  <p class="size-label">1080 x 1920 px (9:16 ratio)</p>

  <article class="ad c1 r1">
    <svg class="hero" viewBox="0 0 440 781">
      <use href="#swoosh"/>
      <rect x="0" y="75" width="400" height="372" clip-path="url(#photo-clip)" style="fill:url(#ph-zip)" role="img" aria-label="Photo of zipscreen blinds on an outdoor patio"/>
      <use href="#red-wash"/>
      <use href="#anniversary-badge"/>
    </svg>
    <h1 class="sale-banner">SALE NOW ON</h1>
    <div class="brand-name"><span class="mark"></span>Portals Drapes &amp; Louvres</div>
    <h2 class="product-ribbon">Zipscreen Blinds</h2>
    <ul class="benefits" style="left:82px"><li>Made to Measure</li><li>Fully Installed</li><li>Wind, Sun &amp; Insect Protection</li></ul>
    <p class="offer">UP TO <em>40%</em> OFF</p>
    <p class="cta">Book a FREE quote TODAY!</p>
    <footer class="contact-bar">
      <span class="phone"><svg viewBox="0 0 18 16"><use href="#icon-phone"/></svg>9471 2658</span>
      <span class="address"><svg viewBox="0 0 14 18"><use href="#icon-pin"/></svg>482 Upper Wattleby Road,<br>Kestrel Heights</span>
    </footer>
  </article>

  <article class="ad c2 r1">
    <svg class="hero" viewBox="0 0 440 781">
      <use href="#swoosh"/>
      <rect x="0" y="75" width="400" height="372" clip-path="url(#photo-clip)" style="fill:url(#ph-awning)" role="img" aria-label="Photo of a striped outdoor awning against the sky"/>
      <use href="#red-wash"/>
      <use href="#anniversary-badge"/>
    </svg>
    <h1 class="sale-banner">SALE NOW ON</h1>
    <div class="brand-name"><span class="mark"></span>Portals Drapes &amp; Louvres</div>
    <h2 class="product-ribbon">Outdoor Awnings</h2>
    <ul class="benefits" style="left:82px"><li>Reduce Heat &amp; Glare</li><li>Energy Saving</li><li>Custom Made</li></ul>
    <p class="offer">UP TO <em>40%</em> OFF</p>
    <p class="cta">Book a FREE quote TODAY!</p>
    <footer class="contact-bar">
      <span class="phone"><svg viewBox="0 0 18 16"><use href="#icon-phone"/></svg>9471 2658</span>
      <span class="address"><svg viewBox="0 0 14 18"><use href="#icon-pin"/></svg>482 Upper Wattleby Road,<br>Kestrel Heights</span>
    </footer>
  </article>

  <article class="ad c3 r1">
    <svg class="hero" viewBox="0 0 440 781">
      <use href="#swoosh"/>
      <rect x="0" y="75" width="400" height="372" clip-path="url(#photo-clip)" style="fill:url(#ph-shutter)" role="img" aria-label="Photo of a bedroom with white plantation shutters"/>
      <use href="#red-wash"/>
      <use href="#anniversary-badge"/>
    </svg>
    <h1 class="sale-banner">SALE NOW ON</h1>
    <div class="brand-name"><span class="mark"></span>Portals Drapes &amp; Louvres</div>
    <h2 class="product-ribbon">Plantation Shutters</h2>
    <ul class="benefits" style="left:62px"><li>Modern &amp; Elegant</li><li>Light &amp; Privacy Control</li><li>Durable &amp; Easy Care</li></ul>
    <p class="offer">FROM <em>$299</em>/SQM</p>
    <p class="cta">Book a FREE quote TODAY!</p>
    <footer class="contact-bar">
      <span class="phone"><svg viewBox="0 0 18 16"><use href="#icon-phone"/></svg>9471 2658</span>
      <span class="address"><svg viewBox="0 0 14 18"><use href="#icon-pin"/></svg>482 Upper Wattleby Road,<br>Kestrel Heights</span>
    </footer>
  </article>

  <article class="ad c1 r2">
    <svg class="hero" viewBox="0 0 440 781">
      <use href="#swoosh"/>
      <rect x="0" y="75" width="400" height="372" clip-path="url(#photo-clip)" style="fill:url(#ph-roller)" role="img" aria-label="Photo of a bright room with roller shutters on the windows"/>
      <use href="#red-wash"/>
      <use href="#anniversary-badge"/>
    </svg>
    <h1 class="sale-banner">SALE NOW ON</h1>
    <div class="brand-name"><span class="mark"></span>Portals Drapes &amp; Louvres</div>
    <h2 class="product-ribbon">Roller Shutters</h2>
    <ul class="benefits" style="left:92px"><li>Security Protection</li><li>Block Heat &amp; Noise</li><li>Total Light Control</li></ul>
    <p class="offer">UP TO <em>40%</em> OFF</p>
    <p class="cta">Book a FREE quote TODAY!</p>
    <footer class="contact-bar">
      <span class="phone"><svg viewBox="0 0 18 16"><use href="#icon-phone"/></svg>9471 2658</span>
      <span class="address"><svg viewBox="0 0 14 18"><use href="#icon-pin"/></svg>482 Upper Wattleby Road,<br>Kestrel Heights</span>
    </footer>
  </article>

  <article class="ad c2 r2">
    <svg class="hero" viewBox="0 0 440 781">
      <use href="#swoosh"/>
      <rect x="0" y="75" width="400" height="372" clip-path="url(#photo-clip)" style="fill:url(#ph-security)" role="img" aria-label="Photo of a mesh security door opening onto a valley view"/>
      <use href="#red-wash"/>
      <use href="#anniversary-badge"/>
    </svg>
    <h1 class="sale-banner">SALE NOW ON</h1>
    <div class="brand-name"><span class="mark"></span>Portals Drapes &amp; Louvres</div>
    <h2 class="product-ribbon">Security Doors</h2>
    <ul class="benefits" style="left:95px"><li>3 Point Locking</li><li>Premium Mesh</li><li>Custom Made</li></ul>
    <p class="offer">FROM <em>$750</em></p>
    <p class="cta order">ORDER NOW</p>
    <footer class="contact-bar">
      <span class="phone"><svg viewBox="0 0 18 16"><use href="#icon-phone"/></svg>9471 2658</span>
      <span class="address"><svg viewBox="0 0 14 18"><use href="#icon-pin"/></svg>482 Upper Wattleby Road,<br>Kestrel Heights</span>
    </footer>
  </article>

  <article class="ad c3 r2">
    <svg class="hero" viewBox="0 0 440 781">
      <use href="#swoosh"/>
      <rect x="0" y="75" width="400" height="372" clip-path="url(#photo-clip)" style="fill:url(#ph-sheer)" role="img" aria-label="Photo of a bedroom with grey block-out blinds and white sheer curtains"/>
      <use href="#red-wash"/>
      <use href="#anniversary-badge"/>
    </svg>
    <h1 class="sale-banner">SALE NOW ON</h1>
    <div class="brand-name"><span class="mark"></span>Portals Drapes &amp; Louvres</div>
    <h2 class="product-ribbon">Blinds &amp; Sheers</h2>
    <ul class="benefits" style="left:82px"><li>Huge Range of Fabrics</li><li>Modern Soft Finish</li><li>Perfect for Any Room</li></ul>
    <p class="offer">UP TO <em>40%</em> OFF</p>
    <p class="cta">Book a FREE quote TODAY!</p>
    <footer class="contact-bar">
      <span class="phone"><svg viewBox="0 0 18 16"><use href="#icon-phone"/></svg>9471 2658</span>
      <span class="address"><svg viewBox="0 0 14 18"><use href="#icon-pin"/></svg>482 Upper Wattleby Road,<br>Kestrel Heights</span>
    </footer>
  </article>
</div>
</body>
</html>
```